Our business name is Quillbrook Pty Ltd and we already have a logo. We would like the same colours that appear in our logo on our marketing material. I have attached our logo for colour consistency. We need a brochure designed that promotes our aerial photography and aerial imaging services. We'd like to use the brochure for electronic marketing purposes in an effort to attract a new client base. We are a new start up business so funds are fairly scarce. We use sophisticated UAV (unmanned aerial vehicle) or RPA - remotely piloted aircraft technology) that captures beautiful video and still images.
Our services are suitable for many types of industries and applications. We have identified at least 10 market sectors ranging, infrastructure inspections such as: gas pipelines, chemical and petrol storage facilities, pipeline and power line inspections, Archeological and geological surveys, vegetation mapping, wildlife surveys, agriculture and horticulture surveys, high end real estate, sport and event marketing. Our plan is to create a series of brochures (1) for each industry to help us market our business.

Our first brochure will focus on environmental management and compliance. We will target other industries down the track. These industries would see our service as helping them meet their compliance and auditing requirements.
We have a brochure that we put together containing words and some (very boring) format. As this will be one of a series of brochures, we'd like to colour code the industries for easy identification. (perhaps a green tab) in the corner to distinguish between our brochures. We have attached our boring brochure as a starting point. If we like the design there will be more work to follow. We want to be able to standardise the format for the other industries we will target. We anticipate needing another 6-8 brochures over the course of the next 2 months.

I have received questions regarding brochure size.  Apologies, I should have indicated in my posting previously.  The brochure is A3 landscape size so it can be folded in half to make 4 A4 pages.  We need to keep printing costs down so the content needs to be  within 4 pages.  I'm about to make some minor changes to the content to try to reduce the amount of text cause I can see this may be a problem.  Look forward to receiving your design. Thanking you in advance for your great work!

Re: Brochure Quillbrook Environmental Compliance and Monitoring Services

I have reduced the amount of text contained in the original version of the brochure making it more succinct and less wordy.  Could you use the least amount of space because we want to be able to use this brochure as both electric marketing and print based.  I have also included additional photos which will give you more to work with.  Thank you for your work in advance!  Regards Marta 

PLEASE NOTE - TEXT HAS BEEN UPDATED (REDUCED TEXT IN BROCHURE). COULD YOU REFER TO VERSION 2 OF QUILLBROOK ENVIRONMENTAL COMPLIANCE AND MONITORING SERVICES BROCHURE UPDATED FRIDAY 17TH.

Thanks Marta 

Hi talented designers working on the Quillbrook Brochure for Environmental Compliance and Monitoring.  I have been asked to upload the EPS version of Quillbrook Logo.  I have just done so.

Regards
Marta 

Hi all, to assist you with the design concept. I feel I need to clarity a number of points.  We are a new technology driven business.  No one else is conducting environmental surveys using this type of sophisticated equipment. We are in the business of providing clients with visual data (aerial images). Could you include grab lines in the brochure that draws attention to this. We us state of the art technology to produce high quality images efficiently, safely and economically. 

Thank you
Marta

Reason: We need additional time to receive and review designs.

Reason: Need additional time to communicate with designers and to review changes. Thank you Marta

I have extended the project date a few days. I have been incredibly impressed by the quality of your work and thank you all for your efforts.  I am waiting on a few revisions by a number of designers and look forward to receiving these changes.  We are close to completion.  Thanking you all again. Marta 

We are targeting a wide range of industry sectors. Specifically, looking at targeting large engineering type consultancies, corporations, government agencies, auditing bodies. Typically, targeting the professional sector who use data to confirm, monitor and make better decisions.

We want the brochure design to be contemporary and modern which reflects what our business does. We use state of the art unmanned aerial technology to capture brilliant visual images and video. So we want our brochure to reflect that we're leaders in the field offering something different - cutting edge approach. I have additional photos that show vegetation mapping, wildlife surveys, agriculture and horticulture applications. Our services would benefit any business that uses visual data to help them make better, more informed decisions.

Business

Serif
Sans Serif

• We would like you to include photo of the UAV equipment/technology shots. This is new technology so we must also educate our clients on what our technology is capable of doing. We are offering a service that is very different so we want to be able to convey the true benefits of our services such as safety, efficiency, cost saving, reliability. We would like to convey these key themes. Credible data enables businesses to make better, faster decisions.
• We are essentially providing visual data in the form of high definition photos and videos. For this particular sector, data could be used for compliance or auditing purposes, planning, measuring, monitoring, evaluating, assessing, marketing. Could you please include these words in the brochure as they capture our service provision. Please note the red photo is infrared images.

```html
<!DOCTYPE html>
<html lang="en">
<head>
<meta charset="utf-8">
<title>Quillbrook Environmental Compliance and Monitoring Brochure</title>
<link href="https://fonts.googleapis.com/css2?family=Arimo:wght@400;700&display=swap" rel="stylesheet">
<style>
:root{
  --stage:#1f1f1f;
  --label:#ffffff;
  --green-light:#9fd163;
  --green-mid:#7dbb45;
  --green-deep:#4f9131;
  --ink:#ffffff;
  --ink-soft:rgba(255,255,255,.9);
  --glow:rgba(255,255,255,.12);
}
*{margin:0;padding:0;box-sizing:border-box}
html,body{width:1200px;height:1000px;overflow:hidden;background:var(--stage);font-family:"Arimo",Arial,sans-serif;color:var(--ink)}
.canvas{position:relative;width:1200px;height:1000px}
.page-label{position:absolute;top:120px;font-size:30px;font-weight:400;color:var(--label);letter-spacing:.5px}
.page-label--back{left:130px}
.page-label--inside{left:700px}

/* back cover */
.back-cover{position:absolute;left:60px;top:240px;width:340px;height:481px;overflow:hidden;
  background:linear-gradient(160deg,var(--green-light) 0%,var(--green-mid) 55%,var(--green-deep) 100%)}
.back-cover__glow{position:absolute;left:-60px;top:-40px;width:420px;height:420px;border-radius:50%;background:var(--glow)}
.back-cover__drone{position:absolute;left:30px;top:40px;width:250px;height:140px;border-radius:45%;
  background:radial-gradient(ellipse at center,rgba(60,110,40,.45),rgba(60,110,40,0) 70%)}
.contact{position:absolute;left:22px;right:22px;top:345px;font-size:8px;line-height:1.25;text-align:center}
.contact__title{font-weight:700;font-size:9px}
.contact__grid{display:flex;justify-content:space-between;text-align:left;margin:6px 10px}
.contact__web{margin-top:8px;font-size:7px}

/* inside spread */
.spread{position:absolute;left:430px;top:240px;width:730px;height:516px;overflow:hidden}
.spread__art{position:absolute;inset:0}
.col{position:absolute;font-size:6.6px;line-height:1.32;color:var(--ink-soft)}
.col p{margin-bottom:7px}
.col h3{font-size:7px;font-weight:700;margin-bottom:6px;letter-spacing:.3px}
.col--about{left:20px;top:60px;width:150px}
.col--system{left:190px;top:28px;width:160px}
.col--services{left:385px;top:28px;width:150px}
.col--services h2{font-size:11px;font-weight:700;margin-bottom:6px}
.col--services p{font-size:10.5px;line-height:1.25;color:var(--ink)}
.col--services .services__second{margin-top:10px}
.col--team{left:555px;top:22px;width:162px;line-height:1.26}
.col--team p{margin-bottom:6px}
.fold{position:absolute;left:365px;top:0;width:1px;height:516px;background:rgba(0,0,0,.12)}
</style>
</head>
<body>
<div class="canvas">
  <div class="page-label page-label--back">BACK COVER</div>
  <div class="page-label page-label--inside">INSIDE PAGE</div>

  <section class="back-cover">
    <div class="back-cover__glow"></div>
    <div class="back-cover__drone" role="img" aria-label="Faint image of the UAV drone in flight"></div>
    <div class="contact">
      <div class="contact__title">CONTACT US</div>
      <div>Find out more about our services by contacting:</div>
      <div class="contact__grid">
        <div>Tom Ardley<br>Principal Scientist<br>61 3 9000 1200<br>Mob: 0400 111 222<br>tom@quillbrook.com.au</div>
        <div>Marta Velkova<br>Business Development Manager<br>61 3 9000 1200<br>Mob: 0400 333 444<br>marta@quillbrook.com.au</div>
      </div>
      <div class="contact__web">Find out more at www.quillbrook.com.au</div>
    </div>
  </section>

  <section class="spread">
    <svg class="spread__art" viewBox="0 0 730 516" width="730" height="516">
      <defs>
        <linearGradient id="spreadGreen" x1="0" y1="0" x2="1" y2="1">
          <stop offset="0" stop-color="#a3d466"/>
          <stop offset=".6" stop-color="#7dbb45"/>
          <stop offset="1" stop-color="#5a9c36"/>
        </linearGradient>
        <linearGradient id="wetland" x1="0" y1="0" x2="0" y2="1"><stop offset="0" stop-color="#8a9a8c"/><stop offset="1" stop-color="#4f6a4a"/></linearGradient>
        <linearGradient id="parkland" x1="0" y1="0" x2="0" y2="1"><stop offset="0" stop-color="#5f8a3c"/><stop offset="1" stop-color="#3f6a2a"/></linearGradient>
        <linearGradient id="blossom" x1="0" y1="0" x2="0" y2="1"><stop offset="0" stop-color="#b9c4a8"/><stop offset="1" stop-color="#4d7a33"/></linearGradient>
        <linearGradient id="lagoon" x1="0" y1="0" x2="0" y2="1"><stop offset="0" stop-color="#c9d1d6"/><stop offset="1" stop-color="#6d8a6e"/></linearGradient>
        <clipPath id="waveClip"><path d="M0,445 C200,455 420,385 730,300 L730,516 L0,516 Z"/></clipPath>
      </defs>
      <rect width="730" height="516" fill="url(#spreadGreen)"/>
      <circle cx="110" cy="230" r="170" fill="rgba(255,255,255,.1)"/>
      <ellipse cx="660" cy="60" rx="90" ry="45" fill="rgba(255,255,255,.12)" role="img" aria-label="Faint image of the UAV drone"/>
      <g clip-path="url(#waveClip)">
        <rect x="0" y="260" width="130" height="256" fill="url(#wetland)" role="img" aria-label="Aerial photo of wetland channels"/>
        <rect x="132" y="260" width="190" height="256" fill="url(#parkland)" role="img" aria-label="Aerial photo of parkland trees and path"/>
        <rect x="324" y="260" width="196" height="256" fill="url(#blossom)" role="img" aria-label="Aerial photo of flowering trees"/>
        <rect x="522" y="260" width="208" height="256" fill="url(#lagoon)" role="img" aria-label="Aerial photo of lagoon and levee"/>
      </g>
      <path d="M0,445 C200,455 420,385 730,300" fill="none" stroke="rgba(255,255,255,.7)" stroke-width="3"/>
      <path d="M0,435 C200,445 420,375 730,288" fill="none" stroke="rgba(255,255,255,.25)" stroke-width="8"/>
    </svg>
    <div class="fold"></div>

    <div class="col col--about">
      <p>Quillbrook is a new technology company providing environmental science services for over 20 years, now driven by cutting edge UAV technology to provide clients with high quality visual data and imaging services.</p>
      <p>We recognise the many benefits associated with UAV technology in environmental monitoring. UAV systems have revolutionised the way aerial spatial data is captured.</p>
      <p>Quillbrook holds an Unmanned Aircraft System Operator Certificate issued by the National Aviation Authority. Our certification reflects our professionalism and commitment to safety standards.</p>
      <p>Collectively, we have a wealth of knowledge and experience across a range of industry sectors. We have extensive experience in photographic, surveying and environmental science. Our team is made up of highly regarded professionals that are passionate about what they do.</p>
      <p>By identifying our clients' needs, our process focuses on consultation. We work with our clients as business partners to determine how best we can add value to achieve efficient, quality outcomes.</p>
      <p>We are proud of our reputation and our ongoing commitment to provide our clients with aerial imaging that is professional, affordable and reliable.</p>
    </div>

    <div class="col col--system">
      <h3>QUILLBROOK UAV SYSTEM</h3>
      <p>Quillbrook undertook extensive research to source the best fit for purpose UAV system currently available. Our UAV is mounted with a Corvane HD video camera and on-board GPS system. The video camera is image stabilised with 20megapixel photo capability. This level of resolution produces brilliant enlarged images that can be used for environmental data collection/monitoring, compliance and auditing purposes.</p>
      <p>The system is designed with GPS position hold function. This feature enables the pilot to lock the unit at specific positions and altitudes to capture the best possible image. The use of the GPS hold function in conjunction with the auto pilot software allows us to capture perfect repeat photography.</p>
      <p>Our sophisticated technology has 10 times zoom feature with the shutter controlled at ground level by the pilot. These functions enable still images and video to be recorded simultaneously. Camera angles are easily controlled whilst in flight. For mapping purposes, the camera can be pointed vertically to produce multiple stitched images.</p>
      <p>Our UAV system enables real time viewing via a wireless on-ground monitor. Quillbrook's Chief Pilot is the only Environmental Scientist in Australia operating UAVs commercially. As a Scientist, he has the technical expertise to analyse points of interest in 'real-time'. Clients benefit from having all the data they need without visiting the site again. Our operations are always geared towards creating efficiency and cost savings for our clients.</p>
    </div>

    <div class="col col--services">
      <h2>OUR SERVICES:</h2>
      <p>As leaders in environmental science, we know how best to utilise UAV systems and technology. We have accumulated years of experience working with clients and applying knowledge to achieve sustainable results.</p>
      <p class="services__second">We understand that collecting visual data, using traditional aircraft is expensive, dangerous and time consuming. Quillbrook provides a low cost, efficient solution that enables our clients to monitor, evaluate, manage and report on environmental change.</p>
    </div>

    <div class="col col--team">
      <h3>QUILLBROOK TEAM</h3>
      <p>Tom Ardley<br>Chief UAV Pilot and Environmental Scientist.<br>Tom is the only environmental scientist in Australia certified by the National Aviation Authority to use UAV technology for commercial purposes. He is acknowledged nationally as an expert on the application and use of technology for environmental monitoring.</p>
      <p>He has over 20 years' experience in the environmental management sector including 15 years in the professional services industry.</p>
      <p>Marta Velkova<br>Business Development &amp; Operations Manager.<br>Marta manages client relations, marketing, systems development, quality assurance and OH&amp;S compliance.</p>
      <p>Marta has held management roles in the corporate sector working for global companies such as Skyline Air, Northvale Motors and Kestrel Defence. Marta has worked in the field of human resources, employee relations and organisational development. She is one of few people in Australia to be accredited by Northvale Motor Group as a Total Quality Management Facilitator &amp; Assessor. She has strong focus on systems compliance having spent a considerable part of her career working with Engineering and Maintenance functions.</p>
    </div>
  </section>
</div>
</body>
</html>
```